Design Project - Finance Website (Only need PSD)

UPDATED PROJECT (Now only PSD needed)
Need a Wordpress design for a company called "Corvale Lending Partners". The company provides finance for corporate clients, businesses and property developers. The design should be business like with appealing colours that communicate trust. I have uploaded a banner and logo to be incorporated or feel free to design something better if you think you can.
** I now only need the PSD
** I want something that is actually designed rather than from a template.
Thanks
Updates
The website will be used for lead generation so the contact form with adjustable fields in the Wordpress backend should be fairly prominent on the page.
I have uploaded a banner and logo for the site. None of the designs I have seen so far were good enough so the first decent design using the new banner and logo provided will win the job. I do not want just a template that has been cut and paste from somewhere else, I want decent design. If anyone provides a decent design then I will give an extra bonus of $150.
Reason: I have uploaded a banner and logo for the site. None of the designs I have seen so far were good enough so the first decent design using the new banner and logo provided will win the job. I do not want just a template that has been cut and paste from somewhere else, I want decent design. If anyone provides a decent design then I will give an extra bonus of $150.
Thanks
Target Market(s)
Business owners & property developers
Industry/Entity Type
Finance
Requirements
Must have
- Contact form on home page that can be altered through the back end eg. ability to add or remove fields. Widgetised sidebars.
Nice to have
- Widgetised footer.

```html
<!DOCTYPE html>
<html lang="en">
<head>
<meta charset="utf-8">
<title>Corvale Lending Partners</title>
<link href="https://fonts.googleapis.com/css2?family=Arimo:wght@400;700&family=Dosis:wght@600&family=PT+Sans+Caption:wght@700&family=PT+Sans+Narrow:wght@700&family=Source+Sans+3:wght@400;600&display=swap" rel="stylesheet">
<style>
:root{
  --bg-blue:#2b6cc0;
  --brand-blue:#1a5aa8;
  --link-blue:#1d5bb4;
  --green:#7cbc1e;
  --text:#666;
  --dark:#333;
  --line:#d6d6d6;
}
*{box-sizing:border-box;margin:0;padding:0}
html,body{width:1161px;height:1200px;overflow:hidden}
body{background:var(--bg-blue);font-family:"Source Sans 3",sans-serif;position:relative}
.page{position:absolute;left:105px;top:0;width:949px;height:1200px;background:#fff;box-shadow:0 0 10px rgba(0,0,0,.35)}
.abs{position:absolute}
.search{left:700px;top:11px;width:190px;height:20px;background:#0b8fe0;border:1px solid #0663a8}
.search svg{position:absolute;left:4px;top:3px}
.social{top:13px;width:16px;height:16px;border-radius:2px}
.social.one{left:902px;background:#3b5a98}
.social.two{left:922px;background:#5ec1ea}
.logo{left:14px;top:44px;display:flex;align-items:center;gap:8px}
.logo-dot{width:22px;height:22px;border-radius:50%;background:var(--green)}
.logo-name{font-family:"Source Sans 3",sans-serif;font-weight:600;font-size:27px;color:var(--brand-blue);line-height:1}
.nav a{position:absolute;top:102px;font-family:"Dosis",sans-serif;font-weight:600;font-size:18px;color:var(--green);text-decoration:none}
.nav a.active{left:385px;top:99px;width:61px;height:34px;background:var(--brand-blue);color:#fff;border-radius:3px 3px 0 0;text-align:center;padding-top:5px}
.banner{left:0;top:132px;width:949px;height:303px;background:linear-gradient(100deg,#2c5fb0 0%,#dfe6ef 25%,#2a5aa8 45%,#6d97cf 55%,#e5ebf2 72%,#1f4f9c 100%)}
.banner-shadow{left:40px;top:432px;width:869px;height:14px;border-radius:50%;background:radial-gradient(ellipse at center,rgba(0,0,0,.18),rgba(0,0,0,0) 70%)}
.steps{left:324px;top:228px;width:592px;height:119px;background:rgba(235,238,242,.88);border-radius:3px;padding:6px 0 0 16px}
.step{display:flex;align-items:center;height:38.5px;font-family:"PT Sans Caption",sans-serif;font-weight:700;font-variant:small-caps;font-size:28px;color:#2d2d2d;letter-spacing:.5px}
.step-num{width:30px;height:30px;border-radius:50%;background:radial-gradient(circle at 40% 35%,#e8e8e8,#7a7a7a);border:2px solid #555;color:#fff;font-family:"Arimo",sans-serif;font-size:16px;font-variant:normal;display:flex;align-items:center;justify-content:center;margin-right:14px}
.welcome-title{left:25px;top:466px;font-family:"PT Sans Narrow",sans-serif;font-weight:700;font-size:29px;color:var(--green)}
.welcome-text{left:26px;top:509px;width:910px;font-size:15.4px;line-height:21.3px;color:var(--text);text-align:justify}
.welcome-text p+p{margin-top:15px}
.widget-title{font-family:"PT Sans Narrow",sans-serif;font-weight:700;font-size:24px;color:var(--brand-blue)}
.box{border:2px solid #ddd;border-radius:3px;background:#fff;padding:12px 8px 0 8px}
.news{left:18px;top:755px;width:299px;height:190px}
.news-item{display:flex;gap:10px;padding:4px 0 10px;border-bottom:1px solid var(--line);margin-bottom:6px}
.news-item:nth-child(3){border-bottom:none;margin-bottom:0}
.thumb{width:36px;height:36px;flex:none;background:linear-gradient(#8a8a8a,#4c4c4c);border:1px solid #999}
.news-item p,.case p{font-size:13.5px;line-height:18px;color:var(--text)}
.more{position:absolute;right:18px;bottom:10px;font-size:13.5px;color:var(--green)}
.arrows{left:286px;top:734px;display:flex;gap:4px}
.arrows span{width:13px;height:13px;border-radius:2px;background:#4f8fd8}
.case{left:338px;top:755px;width:299px;height:190px;padding:12px 10px 0 14px}
.case-art{float:left;width:100px;height:80px;margin-right:8px;background:linear-gradient(90deg,#d62020 0 32%,#56b62a 32% 64%,#2a7fdc 64%)}
.case p{text-align:justify}
.phone-icon{left:656px;top:709px}
.qc-title{left:701px;top:711px;font-family:"PT Sans Narrow",sans-serif;font-weight:700;font-size:30px;color:#555}
.form{left:659px;top:755px;width:275px;height:190px;border:3px solid #cfe0f5;border-radius:10px;background:linear-gradient(#5a9eea,#1d60b8)}
.field{position:absolute;left:20px;width:212px;height:31px;background:linear-gradient(#fff,#ececec);border:1px solid #aac;border-radius:2px;font-size:14px;color:#444;padding:6px 10px}
.check{position:absolute;left:20px;top:138px;display:flex;align-items:center;gap:10px;color:#fff;font-size:14px;letter-spacing:.4px}
.check svg{background:#fff;border-radius:2px}
.submit{position:absolute;left:159px;top:155px;width:74px;height:24px;background:linear-gradient(#a5dc3a,#6bb212);border:1px solid #4d8a0c;font-family:"PT Sans Narrow",sans-serif;font-weight:700;font-size:16px;color:var(--brand-blue);text-align:center;line-height:22px}
.footer-rule{left:0;top:987px;width:949px;height:3px;background:var(--brand-blue)}
.fcol{top:1018px;font-family:"Arimo",sans-serif;font-size:13.5px;line-height:22.3px;color:var(--link-blue)}
.fcol h4{font-size:15px;font-weight:700;margin-bottom:8px}
.fcol.extra{top:1047px}
.flogo{left:756px;top:1012px;display:flex;align-items:center;gap:8px}
.flogo .logo-dot{background:#aaa;width:18px;height:18px}
.flogo .logo-name{color:#999;font-size:21px}
.copy{left:13px;top:1175px;font-size:13px;color:#111}
</style>
</head>
<body>
<div class="page">
  <div class="abs search"><svg width="12" height="12" viewBox="0 0 12 12"><circle cx="7" cy="5" r="3.5" fill="none" stroke="#111" stroke-width="1.6"/><line x1="4.5" y1="7.5" x2="1" y2="11" stroke="#111" stroke-width="2"/></svg></div>
  <span class="abs social one"></span><span class="abs social two"></span>

  <div class="abs logo"><span class="logo-dot"></span><span class="logo-name">Corvale Lending Partners</span></div>

  <nav class="nav">
    <a class="active" href="#">Home</a>
    <a href="#" style="left:463px">About Us</a>
    <a href="#" style="left:560px">Services</a>
    <a href="#" style="left:650px">Finance</a>
    <a href="#" style="left:735px">Real Estate</a>
    <a href="#" style="left:849px">Contact Us</a>
  </nav>

  <div class="abs banner" role="img" aria-label="Glass office towers against a blue cloudy sky"></div>
  <div class="abs banner-shadow"></div>
  <div class="abs steps">
    <div class="step"><span class="step-num">1</span>Compare several capital provider rates</div>
    <div class="step"><span class="step-num">2</span>Access to real estate and hedge funds</div>
    <div class="step"><span class="step-num">3</span>Optimise your capital returns</div>
  </div>

  <h1 class="abs welcome-title">Welcome to Corvale Lending Partners</h1>
  <div class="abs welcome-text">
    <p>Etiam porta tincidunt libero id tincidunt. Sed pharetra eros et nibh tempus aliquet aliquam felis pulvinar. Cras pulvinar ipsum et leo imperdiet at accumsan mauris pharetra. Suspendisse aliquam lacus egestas justo placerat viverra. Nullam nec tellus nisi. Vivamus commodo massa eu nunc blandit commodo. Integer cursus dapibus sem at adipiscing. Mauris scelerisque convallis nulla, a auctor magna pellentesque et.</p>
    <p>Aenean porta, odio ac blandit tempus, ipsum arcu varius arcu, sit amet tempus neque metus sit amet arcu. Pellentesque ut odio eget dui elementum euismod nec ac enim. Quisque mattis mauris ac nisl accumsan euismod. Etiam porttitor ipsum eu eros blandit dapibus. Nullam ultrices mi ac lorem tincidunt vehicula. Nunc in arcu sed leo accumsan posuere. In laoreet molestie rhoncus. Quisque pretium augue sed ipsum imperdiet lacinia. Mauris feugiat tristique faucibus. Cras venenatis ante eu purus condimentum sit amet malesuada erat iaculis.</p>
  </div>

  <h2 class="abs widget-title" style="left:18px;top:721px">Latest News</h2>
  <div class="abs arrows"><span></span><span></span></div>
  <div class="abs box news">
    <div class="news-item"><span class="thumb" role="img" aria-label="Author portrait"></span><p>Lorem ipsum dolor sit amet, conssectur ectetur adipiscing elit.</p></div>
    <div class="news-item"><span class="thumb" role="img" aria-label="Author portrait"></span><p>Morbi iaculis pretium leo, eu faucibus urna ultricies non.</p></div>
    <div class="news-item"><span class="thumb" role="img" aria-label="Author portrait"></span><p>Vestibulum eget augue quam, nec tristique neque.</p></div>
    <span class="more">Read More</span>
  </div>

  <h2 class="abs widget-title" style="left:338px;top:721px">Case Study</h2>
  <div class="abs box case">
    <div class="case-art" role="img" aria-label="Red, green and blue office binders"></div>
    <p>Lorem ipsum dolor sit amet, conssectur ectetur adipiscing elit blandit dapibus posuere laoreet molestic eros.</p>
    <p>Etiam porttitor ipsum eu eros blandit dapibus. Nullam ultrices mi ac lorem tincidunt vehicula. Nunc in arcu sed leo accumsan posuere. In laoreet molestie rhoncus.</p>
    <span class="more">Read More</span>
  </div>

  <svg class="abs phone-icon" width="34" height="36" viewBox="0 0 34 36"><path d="M6 3c3-2 5-1 6 1l3 6c1 2 0 3-2 4l-2 1c1 4 4 8 8 10l2-2c1-1 3-2 4 0l5 5c1 2 0 4-2 5-3 2-7 2-12-2C9 26 4 18 3 11 2 7 3 5 6 3z" fill="#333"/></svg>
  <h2 class="abs qc-title">Quick Contact</h2>
  <form class="abs form">
    <div class="field" style="top:13px">Name*</div>
    <div class="field" style="top:52px">Email Address*</div>
    <div class="field" style="top:91px">Phone</div>
    <div class="check"><svg width="13" height="13" viewBox="0 0 13 13"><path d="M2 7l3 3 6-7" fill="none" stroke="#1a4a90" stroke-width="2.2"/></svg>Subscribe to our Newsletter</div>
    <div class="submit">Submit</div>
  </form>

  <div class="abs footer-rule"></div>
  <div class="abs fcol" style="left:17px"><h4>About Us</h4>Company Info<br>What We Do<br>Clients</div>
  <div class="abs fcol" style="left:134px"><h4>Services</h4>Lorem Ipsum<br>Etiam Portitor<br>Blandit Dapibus</div>
  <div class="abs fcol" style="left:260px"><h4>Finance</h4>Lorem Ipsum<br>Etiam Portitor<br>Blandit Dapibus</div>
  <div class="abs fcol" style="left:385px"><h4>Contact Us</h4>Dana Whitlock<br>Unit 4 Harbour Lane,<br>Fernvale, SA, 5190<br>PO Box 482,<br>Fernvale, SA, 5190</div>
  <div class="abs fcol extra" style="left:533px">Phone Work/Mobile: 0400 555 218<br>Phone: 08 5550 1234<br>Fax: 08 5550 1299<br>Email: dana@corvalelending.example</div>
  <div class="abs flogo"><span class="logo-dot"></span><span class="logo-name">Corvale Lending Partners</span></div>

  <p class="abs copy">© 2012 Corvale Lending Partners. All Rights Reserved.</p>
</div>
</body>
</html>
```